Animal Eye Clinic needs a Business card

We are a new veterinary ophthalmology practice (Ridgeline Pet Vision Care) and we need a business card designed. We only see animal eyes - we are not a regular veterinary clinic. We already have a logo. We are looking for a professional, good looking business card to hand out to our clients. We are looking for something simple but professional and contemporary. Our logo is likely the only picture/graphic that needs to be on the card.
Updates

Contact Information for Business Card

Delia Vossman, BSc, DVM, MSc, DipACVO
Veterinary Ophthalmologist

Phone: 250.418.3927
Email: ridgelinepetvisioncare@mailbox-example.net
Website: ridgelinepetvisioncare-example.net
Address: 1874 Thornbury Rd
Kelowna, BC, V1X 4M9

Colors

Designer to choose colors to be used in the design.

Requirements
Must have
• Our logo (attached)

```html
<!DOCTYPE html>
<html lang="en">
<head>
<meta charset="utf-8">
<title>Ridgeline Pet Vision Care – Business Card</title>
<link rel="stylesheet" href="https://fonts.googleapis.com/css2?family=Arimo:wght@400;700&display=swap">
<style>
  :root {
    --stage: #3a3b3d;
    --card: #231f20;
    --teal: #0797a6;
    --white: #ffffff;
    --text-light: #f2f2f2;
  }
  * { box-sizing: border-box; margin: 0; padding: 0; }
  html, body {
    width: 1200px; height: 900px; overflow: hidden;
    background: var(--stage);
    font-family: "Arimo", Arial, sans-serif;
  }
  .canvas { position: relative; width: 1200px; height: 900px; }

  .card {
    position: absolute;
    width: 600px; height: 343px;
    background: var(--card);
    box-shadow: 0 12px 30px rgba(0,0,0,.45);
    overflow: hidden;
  }
  .card--front { left: 70px; top: 70px; }
  .card--back  { left: 530px; top: 480px; }

  .accent-band {
    position: absolute; right: 0; bottom: 26px;
    width: 56%; height: 13px; display: flex;
  }
  .accent-band__teal { flex: 0 0 56%; background: var(--teal); }
  .accent-band__white { flex: 1; background: var(--white); }

  .brand {
    position: absolute; display: flex; align-items: center; gap: 10px;
    color: var(--teal); font-weight: 700; text-transform: uppercase;
    letter-spacing: .5px; line-height: 1;
  }
  .brand__dot {
    flex: 0 0 auto; border-radius: 50%; background: var(--teal);
  }
  .card--front .brand { left: 150px; top: 140px; font-size: 24px; }
  .card--front .brand__dot { width: 40px; height: 40px; }
  .card--back .brand { left: 40px; top: 118px; font-size: 16px; }
  .card--back .brand__dot { width: 28px; height: 28px; }

  .person {
    position: absolute; right: 34px; top: 34px; text-align: right;
  }
  .person__name {
    color: var(--teal); font-weight: 700; font-size: 23px;
    text-transform: uppercase; letter-spacing: .3px;
  }
  .person__credentials, .person__title {
    color: var(--text-light); font-size: 11.5px; margin-top: 4px;
  }

  .contact {
    position: absolute; left: 292px; top: 166px;
    display: flex; gap: 10px;
  }
  .contact__icons {
    display: flex; flex-direction: column; justify-content: space-around;
    padding: 14px 0; width: 16px;
  }
  .contact__icons svg { width: 14px; height: 14px; }
  .contact__rule { width: 2px; background: var(--teal); }
  .contact__lines {
    list-style: none; color: var(--text-light);
    font-size: 13px; line-height: 23px;
  }
</style>
</head>
<body>
<main class="canvas">

  <section class="card card--front" aria-label="Business card front">
    <div class="brand">
      <span class="brand__dot"></span>
      <span class="brand__name">Ridgeline Pet Vision Care</span>
    </div>
    <div class="accent-band"><span class="accent-band__teal"></span><span class="accent-band__white"></span></div>
  </section>

  <section class="card card--back" aria-label="Business card back">
    <div class="person">
      <h1 class="person__name">Delia Vossman</h1>
      <p class="person__credentials">BSc, DVM, MSc, DipACVO</p>
      <p class="person__title">Veterinary Ophthalmologist</p>
    </div>

    <div class="brand">
      <span class="brand__dot"></span>
      <span class="brand__name">Ridgeline Pet Vision Care</span>
    </div>

    <div class="contact">
      <div class="contact__icons">
        <svg viewBox="0 0 24 24" aria-hidden="true"><path fill="#0797a6" d="M6.6 10.8a15.1 15.1 0 0 0 6.6 6.6l2.2-2.2a1 1 0 0 1 1-.25 11.4 11.4 0 0 0 3.6.57 1 1 0 0 1 1 1V20a1 1 0 0 1-1 1A17 17 0 0 1 3 4a1 1 0 0 1 1-1h3.5a1 1 0 0 1 1 1c0 1.25.2 2.45.57 3.57a1 1 0 0 1-.25 1z"/></svg>
        <svg viewBox="0 0 24 24" aria-hidden="true"><path fill="#0797a6" d="M12 2a7 7 0 0 0-7 7c0 5.2 7 13 7 13s7-7.8 7-13a7 7 0 0 0-7-7zm0 9.5A2.5 2.5 0 1 1 12 6.5a2.5 2.5 0 0 1 0 5z"/></svg>
        <svg viewBox="0 0 24 24" aria-hidden="true"><path fill="#0797a6" d="M3 5h18v14H3zm2 2v.5l7 4.5 7-4.5V7z"/></svg>
        <svg viewBox="0 0 24 24" aria-hidden="true"><g fill="none" stroke="#0797a6" stroke-width="2"><circle cx="12" cy="12" r="9"/><path d="M3 12h18M12 3c3 3.2 3 14.8 0 18M12 3c-3 3.2-3 14.8 0 18"/></g></svg>
      </div>
      <span class="contact__rule"></span>
      <ul class="contact__lines">
        <li>250.418.3927</li>
        <li>1874 Thornbury Rd,</li>
        <li>Kelowna, BC, V1X 4M9</li>
        <li>ridgelinepetvisioncare@mailbox-example.net</li>
        <li>ridgelinepetvisioncare-example.net</li>
      </ul>
    </div>

    <div class="accent-band"><span class="accent-band__teal"></span><span class="accent-band__white"></span></div>
  </section>

</main>
</body>
</html>
```